Construction proffessionals servicing the inner suburbs of Melbournes NorthWest specialising in aler

I would like a web site that is sharp, contemporary and simple to navigate, ie.not too many pages. i would like a home page with some info about us, who we are what our history is and my passion for building and construction based on impeccable customer focus. i would like a projects page and somewhere for clients to add testimonials. i would like a project calculator as well so prospective clients can work out a rough budget prior to contacting. i would like the colours to be in line with my logo which i have uploaded. i have many photos which can be used and can be shared via drop box when required. I would like it to be personal to capture our transparent process. i would like to add our company process as well. be brave and take risks.

Target Market(s)

People renovating and extending their homes, people needing inspections on new homes and pre-purchase inspections

Industry/Entity Type

Construction

Number of Pages Required

5+ page

Requirements
Must have
• Professional, easy to navigate, provide viewers with a happy experience, look great, contacts, project calculator, link through to my training company www.qdmn.learnhub.example also check rowenhq on instagram for pics
Nice to have
• Links to instagram, fonts to match email signature

```html
<!DOCTYPE html>
<html lang="en">
<head>
<meta charset="utf-8">
<title>Rowen Build Group</title>
<link href="https://fonts.googleapis.com/css2?family=Open+Sans:wght@400;600;700&family=Oswald:wght@500&display=swap" rel="stylesheet">
<style>
:root{
  --orange:#f2921f;
  --orange-dark:#d97a0c;
  --ink:#333;
  --muted:#777;
  --dark:#2b2b2b;
  --footer:#3a3a3a;
  --band:#eeeeee;
  --line:#dcdcdc;
  --white:#fff;
}
*{box-sizing:border-box;margin:0;padding:0}
html,body{width:727px;height:1200px;overflow:hidden;background:var(--white)}
body{font-family:"Open Sans",Arial,sans-serif;color:var(--ink);font-size:7px;line-height:1.5}
.page{position:relative;width:727px;height:1200px}

.site-header{height:56px;display:flex;align-items:center;justify-content:space-between;padding:0 42px;border-bottom:1px solid var(--line)}
.brand{display:flex;align-items:center;gap:6px;font-weight:700;font-size:20px;color:var(--orange)}
.brand-square{width:14px;height:14px;background:var(--orange)}
.main-nav{display:flex;align-items:center;gap:20px;font-size:6.5px;font-weight:600;color:var(--muted);text-transform:uppercase}
.main-nav .active{color:var(--orange)}
.nav-btn{background:var(--orange);color:var(--white);padding:6px 12px}

.hero{position:relative;height:296px;background:linear-gradient(180deg,#7c98b8 0%,#9aa7b8 40%,#4d5560 70%,#c48a4a 100%)}
.hero-copy{position:absolute;left:82px;top:110px;display:flex;flex-direction:column;align-items:flex-start;gap:3px;font-family:"Oswald",sans-serif;color:var(--white);text-transform:uppercase}
.hero-copy span{padding:4px 10px;font-size:12px;letter-spacing:.5px}
.hero-copy .dark{background:rgba(40,40,40,.85)}
.hero-copy .accent{background:var(--orange)}
.hero-copy .big{background:var(--orange);font-size:22px;padding:5px 12px}

.welcome{display:flex;gap:30px;padding:36px 42px 0 82px}
.welcome-main{width:370px}
.section-title{font-size:14px;font-weight:700;color:var(--ink)}
.section-title em{font-style:normal;color:var(--orange)}
.welcome-intro{display:flex;gap:10px;margin:14px 0}
.welcome-photo{width:88px;height:58px;background:linear-gradient(135deg,#a9876a,#d6d2c8)}
.welcome-lines{color:var(--orange);font-size:7px;line-height:1.7}
.welcome-text{color:var(--muted)}
.btn{display:inline-block;background:var(--orange);color:var(--white);font-size:6px;font-weight:700;padding:5px 10px;margin-top:14px;text-transform:uppercase}

.calculator{width:160px;margin-top:-2px;border:1px solid var(--line);box-shadow:0 2px 6px rgba(0,0,0,.12)}
.calc-head{background:var(--orange);color:var(--white);font-weight:700;font-size:9px;text-align:center;padding:5px}
.calc-body{padding:8px 10px}
.calc-field{border:1px solid var(--line);height:15px;margin-bottom:6px;padding:3px 5px;color:#aaa;font-size:5.5px}
.calc-btn{display:inline-block;background:var(--dark);color:var(--white);font-size:6px;font-weight:700;padding:5px 10px;margin-top:4px}

.about{position:absolute;top:690px;left:0;width:727px;height:255px;background:var(--band);padding:22px 82px 0}
.cards{display:flex;gap:22px;margin-top:16px}
.card{width:172px}
.card-photo{height:70px;margin-bottom:8px}
.card h3{font-size:8px;font-weight:700;margin-bottom:3px}
.card p{color:var(--muted);font-size:5.5px}
.card .btn{margin-top:8px;padding:4px 8px}

.testimonials{position:absolute;top:975px;left:0;width:727px;padding:0 82px}
.testi-head{display:flex;justify-content:space-between;align-items:center}
.testi-arrow{width:14px;height:14px;border-radius:50%;border:1px solid var(--line)}
.testi-row{display:flex;gap:30px;margin-top:16px}
.testi{display:flex;gap:10px;width:270px}
.testi-photo{flex:none;width:46px;height:46px;border-radius:50%}
.testi p{color:var(--muted);font-size:5.5px}
.testi cite{display:block;color:var(--orange);font-style:normal;font-size:6px;margin-top:4px}

.site-footer{position:absolute;top:1125px;left:0;width:727px;height:75px;background:var(--footer);color:#ccc;font-size:5.5px;padding:14px 82px}
.footer-row{display:flex;justify-content:space-between;align-items:center}
.footer-links{display:flex;gap:14px}
.social{display:flex;gap:5px}
.social span{width:14px;height:14px;border-radius:50%;border:1px solid #aaa}
.footer-bottom{margin-top:16px;border-top:1px solid #555;padding-top:8px}
</style>
</head>
<body>
<div class="page">
  <header class="site-header">
    <div class="brand"><span class="brand-square"></span>RHQ</div>
    <nav class="main-nav">
      <span class="active">Home</span><span>About Us</span><span>Services</span><span>Projects</span><span>News</span><span>Contact Us</span><span class="nav-btn">Login</span>
    </nav>
  </header>

  <section class="hero" role="img" aria-label="City skyline across the river at dusk">
    <div class="hero-copy">
      <span class="dark">Providing quality expert advice,</span>
      <span class="accent">Common sense and friendly</span>
      <span class="big">Professional service</span>
    </div>
  </section>

  <section class="welcome">
    <div class="welcome-main">
      <h1 class="section-title">Welcome to the <em>Rowen Build Group</em> Pty Ltd Website.</h1>
      <div class="welcome-intro">
        <div class="welcome-photo" role="img" aria-label="Renovated period home exterior"></div>
        <div class="welcome-lines">Have we already met?<br>Do you have a building issue?<br>Do you need building advice, or simply someone to help<br>you through the realities of the building process?</div>
      </div>
      <p class="welcome-text">If you answered yes to any of these questions let us help you. Our team was created in 2013 to assist people with the issues that confront consumers, home builders, landlords, purchasers and builders in these modern, technical and too often litigious times. We are here to guide you through every stage of your project with honest, practical advice and clear pricing.</p>
      <span class="btn">Read More</span>
    </div>
    <aside class="calculator">
      <div class="calc-head">Project Calculator</div>
      <div class="calc-body">
        <div class="calc-field">Service</div>
        <div class="calc-field">Project size</div>
        <div class="calc-field">Budget</div>
        <div class="calc-field">Suburb</div>
        <div class="calc-field">Start date</div>
        <div class="calc-field">Email</div>
        <span class="calc-btn">CALCULATE</span>
      </div>
    </aside>
  </section>

  <section class="about">
    <h2 class="section-title">About <em>Us</em></h2>
    <div class="cards">
      <article class="card">
        <div class="card-photo" role="img" aria-label="Construction manager on site" style="background:linear-gradient(135deg,#8d7a66,#cfc2b0)"></div>
        <h3>Construction Manager</h3>
        <p>A rich career spanning residential and commercial builds, bringing careful planning and strong site leadership to every project.</p>
        <span class="btn">Read More</span>
      </article>
      <article class="card">
        <div class="card-photo" role="img" aria-label="Building and construction trainer in a heritage interior" style="background:linear-gradient(135deg,#5e4a3a,#b58f63)"></div>
        <h3>Building and Construction Trainer</h3>
        <p>Teaching building practice for many years, sharing practical skills and standards with the next generation of trades.</p>
        <span class="btn">Read More</span>
      </article>
      <article class="card">
        <div class="card-photo" role="img" aria-label="Commercial building site" style="background:linear-gradient(135deg,#7a8694,#c9c3b6)"></div>
        <h3>Commercial Site Manager</h3>
        <p>Hands on management of large commercial sites, keeping trades, safety and timelines working together smoothly.</p>
        <span class="btn">Read More</span>
      </article>
    </div>
  </section>

  <section class="testimonials">
    <div class="testi-head">
      <h2 class="section-title">Client <em>Testimonials</em></h2>
      <span class="testi-arrow"></span>
    </div>
    <div class="testi-row">
      <div class="testi">
        <div class="testi-photo" role="img" aria-label="Client portrait" style="background:#b9a38f"></div>
        <div>
          <p>The team guided us through our extension with clear advice and honest pricing. Every question was answered and the finished home is better than we hoped for.</p>
          <cite>Mark Ellis, Northvale</cite>
        </div>
      </div>
      <div class="testi">
        <div class="testi-photo" role="img" aria-label="Client portrait" style="background:#a0786a"></div>
        <div>
          <p>Our pre-purchase inspection was thorough and easy to understand. It saved us from a costly mistake and gave us real confidence in our decision.</p>
          <cite>Jane Porter, Northvale</cite>
        </div>
      </div>
    </div>
  </section>

  <footer class="site-footer">
    <div class="footer-row">
      <div class="footer-links"><span>Home</span><span>About Us</span><span>Services</span><span>News</span><span>Testimonials</span><span>Contact Us</span></div>
      <div class="social"><span></span><span></span><span></span><span></span></div>
    </div>
    <div class="footer-row footer-bottom">
      <div class="footer-links"><span>Privacy Policy</span><span>Terms and Conditions</span><span>Sitemap</span></div>
      <span>Copyright © 2013. All Rights Reserved</span>
    </div>
  </footer>
</div>
</body>
</html>
```